Need a redesign for our Wordpress Credit report website

Hi, We need someone to redesign our Wordpress credit report website, lumenledger.co.za. The designer will be responsible for the following pages:
- home page
- blog page
- single post
- dashboard
- credit report page

About LumenLedger.co.za
Lumen Ledger is a consumer focussed credit report platform where South African citizens can get an easy to understand credit report that shows them where to improve their credit scores.

```html
<!DOCTYPE html>
<html lang="en">
<head>
<meta charset="utf-8">
<title>LumenLedger – Check your credit score</title>
<link href="https://fonts.googleapis.com/css2?family=Montserrat:wght@500;600;700;800&family=Libre+Franklin:wght@400;500&display=swap" rel="stylesheet">
<style>
:root{
  --green:#9acd34;
  --green-dark:#86b52a;
  --blue:#2a6fc2;
  --blue-deep:#1d5aa8;
  --ink:#111111;
  --text:#333333;
  --muted:#555555;
  --line:#e4e4e4;
  --field:#f1f1f1;
  --white:#ffffff;
  --footer:#000000;
}
*{margin:0;padding:0;box-sizing:border-box}
html,body{width:1200px;height:2944px;overflow:hidden;background:var(--white)}
body{position:relative;font-family:"Libre Franklin",Arial,sans-serif;color:var(--text)}
.abs{position:absolute}
h1,h2,h3,h4,.head{font-family:"Montserrat",Arial,sans-serif}

/* top bar */
.topbar{left:0;top:0;width:1200px;height:55px;background:var(--green);color:var(--white);font-size:13px}
.topbar .item{position:absolute;top:19px;display:flex;align-items:center;gap:7px}
.topbar .sep{position:absolute;top:12px;width:1px;height:30px;background:rgba(255,255,255,.8)}
.topbar .dots{position:absolute;left:1003px;top:21px;display:flex;gap:9px}
.topbar .dots span{width:11px;height:11px;border-radius:50%;background:var(--white)}

/* nav */
.nav{left:0;top:55px;width:1200px;height:82px;background:var(--white)}
.nav a{position:absolute;top:33px;font-size:15px;color:#333;text-decoration:none}
.nav .active:after{content:"";position:absolute;left:4px;right:4px;top:48px;height:3px;background:var(--green)}
.brand-disc{left:137px;top:17px;width:144px;height:154px;border-radius:50%;background:var(--white);z-index:3}
.brand{left:170px;top:81px;z-index:4;font-family:"Montserrat",sans-serif;font-weight:700;font-size:26px;color:var(--blue)}

/* hero */
.hero{left:0;top:137px;width:1200px;height:686px;background:radial-gradient(ellipse at 70% 30%,#7b7f86 0%,#4a4a4f 40%,#262628 100%)}
.hero-title{left:0;width:1200px;text-align:center;font-weight:800;font-size:48px;color:var(--white);line-height:52px}
.hero-title em{font-style:normal;color:var(--green)}
.hero-sub{left:340px;top:433px;width:500px;text-align:center;font-size:15px;line-height:26px;color:var(--white)}
.btn{display:flex;align-items:center;justify-content:center;background:var(--green);color:var(--white);font-family:"Montserrat",sans-serif;font-weight:700;font-size:17px;border-radius:27px 0 27px 27px}

/* form */
.signup{left:141px;top:679px;width:948px;height:234px;background:var(--blue);border-radius:6px}
.signup h2{position:absolute;top:33px;width:100%;text-align:center;font-size:26px;font-weight:700;color:var(--white)}
.field{position:absolute;width:269px;height:43px;border-radius:22px;background:var(--field);color:#777;font-size:15px;padding:12px 0 0 22px}
.field.submit{background:var(--green);color:var(--white);font-family:"Montserrat",sans-serif;font-weight:700;text-align:center;padding-left:0}

/* features */
.vline{left:611px;top:913px;width:1px;height:647px;background:var(--line)}
.hline{left:0;top:1206px;width:1200px;height:1px;background:var(--line)}
.features-title{left:215px;top:1030px;font-size:42px;font-weight:800;line-height:55px;color:var(--ink)}
.feature-icon{border-radius:10px;background:linear-gradient(135deg,#9acd34 0%,#2b2b2b 100%);opacity:.85}
.feature-text{font-family:"Montserrat",sans-serif;font-weight:600;font-size:23px;line-height:30px;color:var(--ink)}

/* testimonials */
.testi{left:0;top:1560px;width:611px;height:444px;background:var(--green);border-bottom-right-radius:80px}
.testi h2{position:absolute;left:112px;top:92px;font-size:47px;font-weight:700;line-height:52px;color:var(--white)}
.testi p{position:absolute;left:112px;top:203px;width:440px;font-size:15px;line-height:26px;color:var(--white)}
.reviews{left:611px;top:1560px;width:589px;height:444px;background:linear-gradient(120deg,#3b7fcf 0%,#2a6fc2 55%,#1d5aa8 100%);text-align:center;color:var(--white)}
.reviews h2{position:absolute;top:74px;width:100%;font-size:36px;font-weight:800}
.reviews p{position:absolute;left:30px;top:122px;width:529px;font-size:15px;line-height:26px}
.stars{position:absolute;left:0;top:190px;width:100%;display:flex;justify-content:center;gap:5px}
.avatars{position:absolute;top:250px;left:0;width:100%;display:flex;justify-content:center;align-items:center;gap:12px}
.avatars span{border-radius:50%;background:linear-gradient(135deg,#c9d4e3,#7d8fa8);border:2px solid var(--white)}
.reviewer{position:absolute;top:322px;width:100%;font-family:"Montserrat",sans-serif;font-weight:600;font-size:20px}
.count{position:absolute;top:351px;width:100%;font-size:13px}

/* why */
.why-title{left:0;top:2065px;width:1200px;text-align:center;font-size:36px;font-weight:800;color:var(--ink)}
.num{width:58px;height:58px;border-radius:50%;display:flex;align-items:center;justify-content:center;color:var(--white);font-family:"Montserrat",sans-serif;font-weight:700;font-size:25px}
.num.on{background:var(--green)}
.num.off{background:var(--blue)}
.q{left:303px;font-family:"Montserrat",sans-serif;font-weight:600;font-size:22px;color:var(--ink)}
.toggle{left:966px;font-size:28px;font-weight:300;line-height:28px}
.answer{left:309px;top:2246px;width:650px;border-left:2px solid var(--green);padding-left:16px;font-size:15px;line-height:26px;color:var(--text)}

/* footer */
.footer{left:0;top:2592px;width:1200px;height:352px;background:var(--footer);color:var(--white)}
.footer h4{position:absolute;top:68px;font-size:17px;font-weight:700}
.footer .t{position:absolute;font-size:15px;line-height:26px}
.footer .brand-foot{position:absolute;left:112px;top:85px;font-family:"Montserrat",sans-serif;font-weight:700;font-size:28px;color:var(--green)}
.social{position:absolute;left:940px;top:110px;display:flex;gap:7px}
.social span{width:32px;height:32px;border-radius:50%;background:var(--white)}
.divider{position:absolute;left:112px;top:263px;width:976px;height:1px;background:#333}
.copy{position:absolute;top:298px;width:100%;text-align:center;font-size:15px}
</style>
</head>
<body>

<header class="abs topbar">
  <div class="item" style="left:460px"><svg width="12" height="12" viewBox="0 0 24 24" fill="#fff"><path d="M6.6 10.8a15 15 0 0 0 6.6 6.6l2.2-2.2c.3-.3.7-.4 1-.2 1.1.4 2.3.6 3.6.6.6 0 1 .4 1 1V20c0 .6-.4 1-1 1A17 17 0 0 1 3 4c0-.6.4-1 1-1h3.5c.6 0 1 .4 1 1 0 1.3.2 2.5.6 3.6.1.3 0 .7-.2 1z"/></svg>+27 21 555 0142</div>
  <div class="sep" style="left:611px"></div>
  <div class="item" style="left:625px"><svg width="13" height="11" viewBox="0 0 24 18" fill="#fff"><path d="M0 0h24v18H0z" opacity=".0"/><path d="M1 1h22v16H1z" fill="none" stroke="#fff" stroke-width="2"/><path d="M1 1l11 9 11-9" fill="none" stroke="#fff" stroke-width="2"/></svg>info@lumenledger.co.za</div>
  <div class="sep" style="left:820px"></div>
  <div class="item" style="left:887px"><svg width="12" height="12" viewBox="0 0 24 24" fill="#fff"><path d="M10 5l7 7-7 7v-4H2V9h8zM14 3h7v18h-7v-2h5V5h-5z"/></svg>Login</div>
  <div class="sep" style="left:970px"></div>
  <div class="dots"><span></span><span></span><span></span><span></span></div>
</header>

<nav class="abs nav">
  <a class="active" href="#" style="left:488px">Home</a>
  <a href="#" style="left:583px">About</a>
  <a href="#" style="left:679px">Our Services</a>
  <a href="#" style="left:822px">Our Partners</a>
  <a href="#" style="left:964px">Contact Us</a>
</nav>
<div class="abs brand-disc"></div>
<div class="abs brand">LumenLedger</div>

<section class="abs hero" role="img" aria-label="Person typing on a laptop showing a credit score gauge"></section>
<h1 class="abs hero-title" style="top:325px">CHECK YOUR <em>CREDIT SCORE</em></h1>
<h1 class="abs hero-title" style="top:376px"><em>WITHIN</em> SECONDS</h1>
<p class="abs hero-sub">Lorem ipsum dolor sit amet, consectetur adipiscing elit, sed do eiusmod tempor incididunt ut</p>
<a class="abs btn" style="left:506px;top:504px;width:171px;height:53px">GET STARTED</a>

<form class="abs signup">
  <h2>GET STARTED NOW</h2>
  <div class="field" style="left:60px;top:92px">ID Number</div>
  <div class="field" style="left:349px;top:92px">Last Name</div>
  <div class="field" style="left:635px;top:92px">Mobile Number</div>
  <div class="field" style="left:60px;top:152px">First Name</div>
  <div class="field" style="left:349px;top:152px">Primary Email</div>
  <div class="field submit" style="left:635px;top:152px">SHOW MY SCORE</div>
</form>

<div class="abs vline"></div>
<div class="abs hline"></div>
<h2 class="abs features-title">SYSTEM<br>FEATURES:</h2>

<div class="abs feature-icon" style="left:677px;top:985px;width:80px;height:84px" role="img" aria-label="Lightbulb with gears icon"></div>
<p class="abs feature-text" style="left:681px;top:1082px">Dispute generator - easily<br>manage disputes</p>

<div class="abs feature-icon" style="left:209px;top:1226px;width:85px;height:88px" role="img" aria-label="Calculator and budget sheet icon"></div>
<p class="abs feature-text" style="left:209px;top:1324px">Budget tool - easily create<br>a budget</p>

<div class="abs feature-icon" style="left:679px;top:1241px;width:75px;height:77px" role="img" aria-label="Credit card with score gauge icon"></div>
<p class="abs feature-text" style="left:681px;top:1330px">Improve your credit score<br>eBook</p>

<a class="abs btn" style="left:523px;top:1430px;width:171px;height:53px">VIEW ALL</a>

<section class="abs testi">
  <h2>USER<br>TESTIMONIALS</h2>
  <p>The report was accurate and gave me a good understanding of my current credit status. I found it interesting reading the way the scoring worked and really enjoyed reading it...guess because I am doing well with managing credit.</p>
  <svg class="abs" style="left:116px;top:338px" width="60" height="16" viewBox="0 0 60 16" fill="none" stroke="#fff" stroke-width="2"><path d="M15 8H2M7 3L2 8l5 5"/><path d="M38 8h14M47 3l5 5-5 5" stroke="#2a6fc2"/></svg>
</section>

<section class="abs reviews" role="img" aria-label="Smiling man working at a laptop, tinted blue">
  <h2>CLIENT REVIEWS</h2>
  <p>The credit report is easy to use, informative and accurate to the date. Helps me to manage my financial well-being.</p>
  <div class="stars">
    <svg width="15" height="15" viewBox="0 0 24 24" fill="#f5a623"><path d="M12 2l3 7 7 .6-5.4 4.7 1.7 7.2L12 17.8 5.7 21.5l1.7-7.2L2 9.6 9 9z"/></svg>
    <svg width="15" height="15" viewBox="0 0 24 24" fill="#f5a623"><path d="M12 2l3 7 7 .6-5.4 4.7 1.7 7.2L12 17.8 5.7 21.5l1.7-7.2L2 9.6 9 9z"/></svg>
    <svg width="15" height="15" viewBox="0 0 24 24" fill="#f5a623"><path d="M12 2l3 7 7 .6-5.4 4.7 1.7 7.2L12 17.8 5.7 21.5l1.7-7.2L2 9.6 9 9z"/></svg>
    <svg width="15" height="15" viewBox="0 0 24 24" fill="#f5a623"><path d="M12 2l3 7 7 .6-5.4 4.7 1.7 7.2L12 17.8 5.7 21.5l1.7-7.2L2 9.6 9 9z"/></svg>
    <svg width="15" height="15" viewBox="0 0 24 24" fill="#f5a623"><path d="M12 2l3 7 7 .6-5.4 4.7 1.7 7.2L12 17.8 5.7 21.5l1.7-7.2L2 9.6 9 9z"/></svg>
  </div>
  <div class="avatars">
    <span style="width:36px;height:36px"></span>
    <span style="width:44px;height:44px"></span>
    <span style="width:58px;height:58px"></span>
    <span style="width:44px;height:44px"></span>
    <span style="width:36px;height:36px"></span>
  </div>
  <div class="reviewer">Thandi Mokoena</div>
  <div class="count">28 reviews</div>
</section>

<h2 class="abs why-title">WHY GET YOUR SCORE FROM US?</h2>

<div class="abs num on" style="left:219px;top:2161px">01</div>
<h3 class="abs q" style="top:2175px">We don't abuse your personal information:</h3>
<div class="abs toggle" style="top:2175px;color:var(--green)">–</div>
<p class="abs answer">Lorem ipsum dolor sit amet, consectetur adipiscing elit, sed do eiusmod tempor incididunt ut labore et dolore magna aliqua. Quis ipsum suspendisse ultrices gravida. Risus commodo viverra maecenas accumsan lacus vel facilisis.</p>

<div class="abs num off" style="left:219px;top:2362px">02</div>
<h3 class="abs q" style="top:2377px">Our report is super easy to understand:</h3>
<div class="abs toggle" style="top:2377px;color:var(--blue)">+</div>

<div class="abs num off" style="left:219px;top:2454px">03</div>
<h3 class="abs q" style="top:2468px">300,000 + South Africans have trusted us:</h3>
<div class="abs toggle" style="top:2468px;color:var(--blue)">+</div>

<footer class="abs footer">
  <div class="brand-foot">LumenLedger</div>
  <p class="t" style="left:112px;top:158px;width:270px">Lorem ipsum dolor sit amet, consectetur adipiscing elit, sed do eiusmod tempor incididunt</p>

  <h4 style="left:431px">CONTACT US</h4>
  <svg class="abs" style="left:432px;top:110px" width="10" height="14" viewBox="0 0 10 14" fill="#fff"><path d="M5 0a5 5 0 0 1 5 5c0 4-5 9-5 9S0 9 0 5a5 5 0 0 1 5-5zm0 3a2 2 0 1 0 0 4 2 2 0 0 0 0-4z"/></svg>
  <p class="t" style="left:453px;top:103px;width:230px">14 Ledger Lane, Sea Point, Cape Town</p>
  <svg class="abs" style="left:432px;top:172px" width="12" height="12" viewBox="0 0 24 24" fill="#fff"><path d="M6.6 10.8a15 15 0 0 0 6.6 6.6l2.2-2.2c.3-.3.7-.4 1-.2 1.1.4 2.3.6 3.6.6.6 0 1 .4 1 1V20c0 .6-.4 1-1 1A17 17 0 0 1 3 4c0-.6.4-1 1-1h3.5c.6 0 1 .4 1 1 0 1.3.2 2.5.6 3.6.1.3 0 .7-.2 1z"/></svg>
  <p class="t" style="left:453px;top:166px">+27 21 555 0142</p>
  <svg class="abs" style="left:432px;top:209px" width="14" height="11" viewBox="0 0 24 18"><path d="M1 1h22v16H1z" fill="none" stroke="#fff" stroke-width="2"/><path d="M1 1l11 9 11-9" fill="none" stroke="#fff" stroke-width="2"/></svg>
  <p class="t" style="left:455px;top:202px">info@lumenledger.co.za</p>

  <h4 style="left:725px">PURCHASE</h4>
  <p class="t" style="left:727px;top:98px">Delivery Policy</p>
  <p class="t" style="left:727px;top:128px">Data Policy</p>
  <p class="t" style="left:727px;top:158px">Refund Policy</p>
  <p class="t" style="left:727px;top:188px">Charges And Fees</p>

  <h4 style="left:941px">FOLLOW US</h4>
  <div class="social"><span></span><span></span><span></span><span></span></div>

  <div class="divider"></div>
  <p class="copy">©Copyrights 2022 LumenLedger | All rights reserved</p>
</footer>

</body>
</html>
```